Business Card for Professional Photographer

I'm looking for an eye catching modern clean design that compliments my logo/ website fonts & colours.
I specialise in architecture, corporate & commercial photography so I'm marketing to professional clients rather than portrait / wedding clients.

I would prefer to not have a solid black design.

My logo brand guide is as follows :

Main front font. : Reislust
Main font colour : #fff
Slogan front font : Ubuntu Bold
Monogram front font : Venti Medium
Container colour : #fff

I need print ready files in pdf .png & .eps formats.

Included in the files below are some screen grabs as reference to font & colours etc.

```html
<!DOCTYPE html>
<html lang="en">
<head>
<meta charset="UTF-8">
<title>Clear Angle – Business Card</title>
<link rel="stylesheet" href="https://fonts.googleapis.com/css2?family=Josefin+Sans:wght@300;400&family=Nunito:wght@400;800&display=swap">
<style>
  :root {
    --backdrop: #e4e4e2;
    --gold-deep: #bd8c48;
    --gold-mid: #d8b76c;
    --gold-pale: #f6eea6;
    --gold-ink: #b98a45;
    --paper: #ffffff;
    --ink: #2e2e2e;
    --ink-soft: #555555;
  }
  * { margin: 0; padding: 0; box-sizing: border-box; }
  html, body {
    width: 1200px;
    height: 900px;
    overflow: hidden;
    background: var(--backdrop);
  }
  .sheet {
    width: 1200px;
    height: 900px;
    display: flex;
    flex-direction: column;
    align-items: center;
    justify-content: center;
    gap: 40px;
  }
  .card {
    width: 700px;
    height: 400px;
    border-radius: 26px;
    position: relative;
    overflow: hidden;
    box-shadow: 0 8px 24px rgba(0,0,0,0.18);
  }
  .card--front {
    background: linear-gradient(100deg, var(--gold-deep) 0%, var(--gold-mid) 50%, var(--gold-pale) 100%);
  }
  .card--back { background: var(--paper); }

  .brand {
    position: absolute;
    display: flex;
    align-items: center;
    gap: 20px;
  }
  .card--front .brand { left: 50%; top: 50%; transform: translate(-50%, -50%); }
  .card--back .brand { left: 50%; top: 70px; transform: translateX(-50%); }

  .brand__dot {
    width: 64px;
    height: 64px;
    border-radius: 50%;
    border: 3px solid currentColor;
    flex: none;
  }
  .brand__text { display: flex; flex-direction: column; }
  .brand__name {
    font-family: "Josefin Sans", sans-serif;
    font-weight: 300;
    font-size: 34px;
    letter-spacing: 6px;
    text-transform: uppercase;
    line-height: 1;
  }
  .brand__tagline {
    font-family: "Josefin Sans", sans-serif;
    font-weight: 400;
    font-size: 9px;
    letter-spacing: 3px;
    margin-top: 6px;
  }
  .card--front .brand { color: var(--paper); }
  .card--back .brand { color: var(--gold-ink); }

  .person {
    position: absolute;
    left: 0;
    right: 0;
    top: 218px;
    text-align: center;
  }
  .person__name {
    font-family: "Nunito", sans-serif;
    font-weight: 800;
    font-size: 22px;
    color: var(--gold-ink);
  }
  .person__role {
    font-family: "Nunito", sans-serif;
    font-weight: 400;
    font-size: 14px;
    color: var(--ink-soft);
    margin-top: 2px;
  }
  .rule {
    position: absolute;
    left: 50px;
    right: 50px;
    top: 290px;
    height: 1.5px;
    background: linear-gradient(90deg, var(--gold-deep), var(--gold-pale));
  }
  .contact {
    position: absolute;
    left: 0;
    right: 0;
    top: 312px;
    display: flex;
    justify-content: center;
    gap: 18px;
    font-family: "Nunito", sans-serif;
    font-size: 13px;
    color: var(--ink);
  }
  .contact__label { color: var(--gold-ink); font-weight: 800; }
</style>
</head>
<body>
<main class="sheet">
  <section class="card card--front" aria-label="Card front">
    <div class="brand">
      <span class="brand__dot"></span>
      <div class="brand__text">
        <span class="brand__name">Clear Angle</span>
        <span class="brand__tagline">Architecture Corporate Commercial</span>
      </div>
    </div>
  </section>

  <section class="card card--back" aria-label="Card back">
    <div class="brand">
      <span class="brand__dot"></span>
      <div class="brand__text">
        <span class="brand__name">Clear Angle</span>
        <span class="brand__tagline">Architecture Corporate Commercial</span>
      </div>
    </div>
    <div class="person">
      <p class="person__name">Laura Benetti</p>
      <p class="person__role">Development Manager</p>
    </div>
    <div class="rule"></div>
    <p class="contact">
      <span><span class="contact__label">P</span> : 0412 555 019</span>
      <span><span class="contact__label">M</span> : laura@clearanglestudio.com.au</span>
      <span><span class="contact__label">W</span> : www.clearanglestudio.com.au</span>
    </p>
  </section>
</main>
</body>
</html>
```